Cedar Brook Stables, LLC

Equestrian business card to promote equine retirement, farm sitting, short term board. Located in Aiken, SC.
Updates
Updated color schemes.
Contact Information for Business Card
Contact info, description of work.
Colors
0094D4
00A9DD
6FCCEA
C7EBF8
E9F6FB
59FF00
82FF00
B8FF75
E3FFCB
F4FFEA
F0912C
F2A743
F7CA91
FBE8D2
FDF5EE

```html
<!DOCTYPE html>
<html lang="en">
<head>
<meta charset="utf-8">
<title>Cedar Brook Stables, LLC – Business Card</title>
<link href="https://fonts.googleapis.com/css2?family=Poppins:wght@400;500;600&display=swap" rel="stylesheet">
<style>
  :root {
    --backdrop: #2b2b2b;
    --card-white: #ffffff;
    --brand-green: #006b00;
    --ink: #2e2e2e;
    --sun-yellow: #ffd23a;
    --paper-white: #ffffff;
  }
  * { box-sizing: border-box; margin: 0; padding: 0; }
  html, body {
    width: 1093px; height: 1200px; overflow: hidden;
    background: var(--backdrop);
    font-family: "Poppins", sans-serif;
  }
  .stage { position: relative; width: 1093px; height: 1200px; }

  .card {
    position: absolute;
    left: 265px;
    width: 579px;
    height: 356px;
    border-radius: 26px;
  }
  .card--front { top: 226px; background: var(--card-white); }
  .card--back  { top: 621px; width: 582px; background: var(--brand-green); }

  /* Front */
  .person { position: absolute; left: 37px; top: 58px; }
  .person__name {
    font-weight: 600; font-size: 22px; line-height: 1;
    color: var(--brand-green); letter-spacing: 0.3px;
  }
  .person__role {
    font-weight: 400; font-size: 17px; line-height: 1.15;
    color: var(--ink); margin-top: 2px;
  }

  .brand-mark {
    position: absolute; left: 312px; top: 40px; width: 240px;
    display: flex; flex-direction: column; align-items: center; gap: 14px;
  }
  .brand-mark__dot {
    width: 108px; height: 108px; border-radius: 50%;
    background: var(--brand-green);
  }
  .brand-mark__name {
    font-weight: 600; font-size: 21px; line-height: 1.25;
    text-align: center; color: var(--ink); letter-spacing: 1px;
    text-transform: uppercase;
  }
  .card--back .brand-mark { left: 141px; top: 50px; width: 300px; gap: 14px; }
  .card--back .brand-mark__dot { background: var(--sun-yellow); width: 130px; height: 130px; }
  .card--back .brand-mark__name { color: var(--paper-white); font-size: 25px; }

  .contact-list {
    position: absolute; left: 37px; top: 262px; list-style: none;
  }
  .contact-list li {
    display: flex; align-items: center; gap: 7px;
    font-size: 17px; line-height: 21px; color: var(--ink);
  }
  .contact-list svg { width: 16px; height: 16px; flex: none; }
  .accent { color: var(--brand-green); }

  .address {
    position: absolute; right: 33px; top: 286px;
    font-size: 17px; line-height: 21px; text-align: right; color: var(--ink);
    font-style: normal;
  }

  /* Back */
  .services {
    position: absolute; left: 0; right: 0; top: 294px;
    display: flex; justify-content: center; align-items: center; gap: 8px;
    font-weight: 500; font-size: 17px; color: var(--paper-white);
    list-style: none;
  }
  .services__sep {
    width: 9px; height: 9px; border-radius: 50%; background: var(--sun-yellow);
  }
</style>
</head>
<body>
<main class="stage">

  <section class="card card--front" aria-label="Business card front">
    <header class="person">
      <h1 class="person__name">DANIEL HARPER</h1>
      <p class="person__role">Managing Director</p>
    </header>

    <div class="brand-mark">
      <span class="brand-mark__dot" aria-hidden="true"></span>
      <p class="brand-mark__name">Cedar Brook Stables, LLC</p>
    </div>

    <ul class="contact-list">
      <li>
        <svg viewBox="0 0 24 24" aria-hidden="true"><path fill="#006b00" d="M6.6 10.8a15.1 15.1 0 0 0 6.6 6.6l2.2-2.2a1 1 0 0 1 1-.25 11.4 11.4 0 0 0 3.6.57 1 1 0 0 1 1 1V20a1 1 0 0 1-1 1A17 17 0 0 1 3 4a1 1 0 0 1 1-1h3.5a1 1 0 0 1 1 1c0 1.250.2 2.450.57 3.57a1 1 0 0 1-.25 1z"/></svg>
        044-803 215 476
      </li>
      <li>
        <svg viewBox="0 0 24 24" aria-hidden="true"><rect x="2" y="5" width="20" height="14" fill="#006b00"/><path d="M2 5l10 8 10-8" fill="none" stroke="#fff" stroke-width="1.6"/></svg>
        info@cedarbrook.com
      </li>
      <li>
        <svg viewBox="0 0 24 24" aria-hidden="true"><g fill="none" stroke="#006b00" stroke-width="1.8"><circle cx="12" cy="12" r="9.5"/><ellipse cx="12" cy="12" rx="4.2" ry="9.5"/><path d="M2.5 12h19M4 7h16M4 17h16"/></g></svg>
        <span>www.<span class="accent">cedarbrookstables</span>.com</span>
      </li>
    </ul>

    <address class="address">
      421 Paddock Hollow Lane<br>
      00000, Country Name
    </address>
  </section>

  <section class="card card--back" aria-label="Business card back">
    <div class="brand-mark">
      <span class="brand-mark__dot" aria-hidden="true"></span>
      <p class="brand-mark__name">Cedar Brook Stables, LLC</p>
    </div>

    <ul class="services">
      <li>SHORT TERM BOARD</li>
      <li class="services__sep" aria-hidden="true"></li>
      <li>FARM SITTING</li>
      <li class="services__sep" aria-hidden="true"></li>
      <li>EQUINE RETIREMENT</li>
    </ul>
  </section>

</main>
</body>
</html>
```